Professional Business card

I need a business card to send with all my shipments. It needs to look very professional as I am branding myself, more than I am branding my company. The website is not active yet but that along with the instagram is very important as this will be moving shortly. The next required to be included is listed

Target Market(s)

All

Contact Information for Business Card

Very professional and sleek, I am trying to look like the CEO, motivational speaker and future president I plan to be

Colors
ffcf3e

Requirements
Must have
• Front

Dale Wrenfield
CEO
Brivolt Franchiser
Business Consultant/Start Up Guidance
Motivational Speaker
President of The United States 2040
www.dalewrenfield-example.com
[Instagram] @dalewrenfield

Back
I teach the success method used by my company you just bought from. Learn the unique model and start your own Brivolt franchise today
Nice to have
• Black and Gold lettering
Should not have
• Playful vibes

```html
<!DOCTYPE html>
<html lang="en">
<head>
<meta charset="utf-8">
<title>Dale Wrenfield — Business Card</title>
<link href="https://fonts.googleapis.com/css2?family=Lato:wght@400;700;900&display=swap" rel="stylesheet">
<style>
  :root {
    --page-bg: #3a3b3d;
    --card-black: #050505;
    --gold: #ffcf3e;
    --ink: #141414;
    --rule: #e8e8e8;
  }
  * { margin: 0; padding: 0; box-sizing: border-box; }
  html, body {
    width: 1200px; height: 1000px; overflow: hidden;
    background: var(--page-bg);
    font-family: "Lato", "Helvetica Neue", Arial, sans-serif;
  }
  .stage {
    position: relative; width: 1200px; height: 1000px;
  }
  .card {
    position: absolute;
    width: 560px; height: 320px;
    background: var(--card-black);
    border-radius: 26px;
    overflow: hidden;
  }
  .card--front { left: 320px; top: 130px; }
  .card--back  { left: 320px; top: 550px; }

  /* Front */
  .front__name {
    position: absolute; left: 0; right: 0; top: 112px;
    text-align: center;
    color: var(--gold);
    font-weight: 900;
    font-size: 42px;
    letter-spacing: 5px;
    text-transform: uppercase;
    line-height: 1;
  }
  .front__band {
    position: absolute; left: 0; right: 0; top: 166px; height: 42px;
    background: var(--gold);
    display: flex; align-items: center; justify-content: center;
  }
  .front__title {
    color: var(--ink);
    font-weight: 900;
    font-size: 19px;
    letter-spacing: 1.5px;
  }
  .front__social {
    position: absolute; left: 0; right: 0; top: 228px;
    display: flex; align-items: center; justify-content: center; gap: 10px;
    color: var(--gold);
    font-size: 18px;
    letter-spacing: 1px;
  }
  .front__social svg { display: block; }

  /* Back */
  .back__roles {
    position: absolute; inset: 0;
    display: flex; flex-direction: column; align-items: center; justify-content: center;
    color: var(--gold);
    font-size: 21px;
    letter-spacing: 1.5px;
    text-align: center;
    line-height: 1.2;
  }
  .back__rule {
    width: 28px; height: 1.5px; background: var(--rule);
    margin: 9px 0;
  }
  .back__web { letter-spacing: 2px; }
</style>
</head>
<body>
<main class="stage">
  <section class="card card--front" aria-label="Card front">
    <h1 class="front__name">Dale Wrenfield</h1>
    <div class="front__band">
      <p class="front__title">President of The United States 2040</p>
    </div>
    <p class="front__social">
      <svg width="16" height="16" viewBox="0 0 16 16" aria-hidden="true"><circle cx="8" cy="8" r="7" fill="var(--gold)"/></svg>
      <span>@dalewrenfield</span>
    </p>
  </section>

  <section class="card card--back" aria-label="Card back">
    <div class="back__roles">
      <p>Brivolt Franchiser</p>
      <span class="back__rule"></span>
      <p>Business Consultant /<br>Start Up Guidance</p>
      <span class="back__rule"></span>
      <p>Motivational Speaker</p>
      <span class="back__rule"></span>
      <p class="back__web">www.dalewrenfield-example.com</p>
    </div>
  </section>
</main>
</body>
</html>
```